Hvac and insulation company needs good looking business card design

We are hvac and insulation company and looking for a new business cards that look to today standards designs

Target Market(s)

homeowners

Industry/Entity Type

Hvac

Contact Information for Business Card

Name: Walter Brinoku
Home comfort consultant
address: 4827 Dunmore St #215 Oakland, CA 94619
office: 888-316-2790
cell: 510-742-3185
Lic.# 584261
Email: walter@corvane-hvac.com
Web: corvane-hvac.com

Requirements
Must have
• clean and sleek look
Nice to have
• simple with a clean look
Should not have
• to busy business card

```html
<!DOCTYPE html>
<html lang="en">
<head>
<meta charset="utf-8">
<title>Corvane Home Solutions – Business Card</title>
<link href="https://fonts.googleapis.com/css2?family=Open+Sans:wght@400;600;700&display=swap" rel="stylesheet">
<style>
  :root {
    --backdrop: #1c1c1c;
    --card: #111111;
    --orange: #f28a1e;
    --ink-light: #ececec;
    --ink-muted: #8c8c8c;
  }
  html, body {
    margin: 0;
    width: 1200px;
    height: 900px;
    overflow: hidden;
    background: var(--backdrop);
    font-family: "Open Sans", Arial, sans-serif;
  }
  .card {
    position: absolute;
    top: 295px;
    width: 540px;
    height: 310px;
    background: var(--card);
    border-radius: 18px;
    box-shadow: 0 10px 30px rgba(0,0,0,0.45);
    overflow: hidden;
  }
  .card--contact { left: 40px; }
  .card--brand { left: 620px; }

  /* Contact side */
  .contact-brand {
    position: absolute;
    left: 40px;
    top: 128px;
    display: flex;
    align-items: center;
    gap: 10px;
  }
  .contact-brand__dot {
    width: 22px;
    height: 22px;
    border-radius: 50%;
    background: var(--orange);
  }
  .contact-brand__name {
    color: var(--orange);
    font-weight: 700;
    font-size: 40px;
    line-height: 1;
    letter-spacing: -0.5px;
  }
  .contact-details {
    position: absolute;
    left: 300px;
    top: 58px;
    color: var(--ink-light);
  }
  .person-name {
    margin: 0;
    color: var(--orange);
    font-weight: 700;
    font-size: 16px;
    letter-spacing: 0.3px;
    text-transform: uppercase;
  }
  .person-role {
    margin: 2px 0 18px;
    font-size: 13px;
  }
  .contact-list {
    list-style: none;
    margin: 0 0 16px;
    padding: 0;
    font-size: 13px;
  }
  .contact-list li {
    display: flex;
    align-items: center;
    gap: 8px;
    height: 19px;
  }
  .contact-list svg {
    width: 12px;
    height: 12px;
    fill: var(--orange);
    flex: none;
  }
  .address {
    margin: 0;
    font-size: 13px;
    line-height: 1.4;
    font-style: normal;
  }

  /* Brand side */
  .brand-lockup {
    position: absolute;
    left: 0;
    right: 0;
    top: 98px;
    display: flex;
    justify-content: center;
    align-items: center;
    gap: 14px;
  }
  .brand-lockup__dot {
    width: 34px;
    height: 34px;
    border-radius: 50%;
    background: var(--orange);
  }
  .brand-lockup__text { display: flex; flex-direction: column; }
  .brand-name {
    color: var(--orange);
    font-weight: 700;
    font-size: 54px;
    line-height: 0.95;
    letter-spacing: -0.5px;
  }
  .brand-tagline {
    color: var(--ink-muted);
    font-size: 17px;
    letter-spacing: 3px;
    margin-left: 4px;
  }
  .license {
    position: absolute;
    left: 0;
    right: 0;
    top: 206px;
    text-align: center;
    color: var(--orange);
    font-size: 12px;
  }
</style>
</head>
<body>

<section class="card card--contact">
  <div class="contact-brand">
    <span class="contact-brand__dot"></span>
    <span class="contact-brand__name">corvane</span>
  </div>

  <div class="contact-details">
    <h1 class="person-name">Walter Brinoku</h1>
    <p class="person-role">Home Comfort Consultant</p>
    <ul class="contact-list">
      <li>
        <svg viewBox="0 0 16 16" aria-hidden="true"><path d="M3.5 1.5l2.5 0 1.2 3-1.7 1.2a8 8 0 0 0 4.8 4.8l1.2-1.7 3 1.2v2.5a1.5 1.5 0 0 1-1.5 1.5A12.5 12.5 0 0 1 2 3a1.5 1.5 0 0 1 1.5-1.5z"/></svg>
        888-316-2790
      </li>
      <li>
        <svg viewBox="0 0 16 16" aria-hidden="true"><path d="M4.5 1h7a1 1 0 0 1 1 1v12a1 1 0 0 1-1 1h-7a1 1 0 0 1-1-1V2a1 1 0 0 1 1-1zm.5 2v9h6V3zm3 10a.7.7 0 1 0 0 1.4A.7.7 0 0 0 8 13z"/></svg>
        510-742-3185
      </li>
      <li>
        <svg viewBox="0 0 16 16" aria-hidden="true"><path d="M1.5 3h13a.5.5 0 0 1 .5.5v9a.5.5 0 0 1-.5.5h-13a.5.5 0 0 1-.5-.5v-9a.5.5 0 0 1 .5-.5zm.8 1.3L8 8.6l5.7-4.3z"/></svg>
        walter@corvane-hvac.com
      </li>
      <li>
        <svg viewBox="0 0 16 16" aria-hidden="true"><path d="M8 1a7 7 0 1 0 0 14A7 7 0 0 0 8 1zm0 1.5c.8 0 1.7 1.6 2 4H6c.3-2.4 1.2-4 2-4zM6 9.5h4c-.3 2.4-1.2 4-2 4s-1.7-1.6-2-4zM2.6 6.5a5.5 5.5 0 0 1 2.6-3.3c-.4 1-.6 2.1-.7 3.3zm0 3h1.9c.1 1.2.3 2.3.7 3.3a5.5 5.5 0 0 1-2.6-3.3zm10.8-3h-1.9c-.1-1.2-.3-2.3-.7-3.3a5.5 5.5 0 0 1 2.6 3.3zm0 3a5.5 5.5 0 0 1-2.6 3.3c.4-1 .6-2.1.7-3.3z"/></svg>
        corvane-hvac.com
      </li>
    </ul>
    <address class="address">4827 Dunmore St #215<br>Oakland, CA 94619</address>
  </div>
</section>

<section class="card card--brand">
  <div class="brand-lockup">
    <span class="brand-lockup__dot"></span>
    <div class="brand-lockup__text">
      <span class="brand-name">corvane</span>
      <span class="brand-tagline">home solutions</span>
    </div>
  </div>
  <p class="license">Lic.# 584261</p>
</section>

</body>
</html>
```